Realty Group Needs Classy, Contemporary Letterhead Design

We need a letterhead design for a new realty company located in NY, USA. We buy investment properties to rehabilitate and or keep in our rental portfolio.

```html
<!DOCTYPE html>
<html lang="en">
<head>
<meta charset="UTF-8">
<title>Meridian Realty Group, LLC — Letterhead</title>
<link href="https://fonts.googleapis.com/css2?family=Montserrat:wght@700&family=Mulish:wght@400&display=swap" rel="stylesheet">
<style>
  :root {
    --backdrop: #e9eaec;
    --paper: #ffffff;
    --band: #d3d4d6;
    --band-soft: #d9dadc;
    --brand: #4b3a87;
    --ink: #4b3a87;
    --emblem-tone: #ebebec;
  }
  * { margin: 0; padding: 0; box-sizing: border-box; }
  html, body {
    width: 1000px;
    height: 1200px;
    overflow: hidden;
    background: var(--backdrop);
  }
  .letterhead {
    position: absolute;
    left: 35px;
    top: 0;
    width: 930px;
    height: 1200px;
    background: var(--paper);
    overflow: hidden;
  }
  .letterhead__art {
    position: absolute;
    inset: 0;
    width: 100%;
    height: 100%;
  }
  .brand-name {
    position: absolute;
    left: 52px;
    top: 100px;
    font-family: "Montserrat", sans-serif;
    font-weight: 700;
    font-size: 24px;
    color: var(--brand);
    letter-spacing: 0.2px;
    white-space: nowrap;
  }
  .address {
    position: absolute;
    right: 58px;
    top: 119px;
    font-family: "Mulish", sans-serif;
    font-size: 14px;
    line-height: 17px;
    color: var(--ink);
    text-align: right;
  }
  .address__icon {
    width: 14px;
    height: 13px;
    vertical-align: -1px;
    margin-right: 4px;
    fill: var(--ink);
  }
  .contact-list {
    position: absolute;
    left: 52px;
    top: 1036px;
    list-style: none;
    font-family: "Mulish", sans-serif;
    font-size: 14px;
    color: var(--ink);
  }
  .contact-list__item {
    display: flex;
    align-items: center;
    height: 29.5px;
  }
  .contact-list__icon {
    width: 12px;
    height: 12px;
    margin-right: 7px;
    fill: none;
    stroke: var(--ink);
    stroke-width: 1.4;
  }
  .contact-list__icon--solid { fill: var(--ink); stroke: none; }
</style>
</head>
<body>
  <main class="letterhead">
    <svg class="letterhead__art" viewBox="0 0 814 1052" preserveAspectRatio="none" aria-hidden="false">
      <defs>
        <radialGradient id="emblem-glow" cx="0.55" cy="0.55" r="0.55">
          <stop offset="0" stop-color="#e6e6e7"/>
          <stop offset="1" stop-color="#e6e6e7" stop-opacity="0"/>
        </radialGradient>
      </defs>
      <!-- header band -->
      <path class="header-band" d="M0,0 H814 V122 C800,140 770,162 730,165 C640,170 560,115 420,70 C260,20 120,20 0,84 Z" fill="var(--band)"/>
      <path class="header-rule" d="M0,84 C120,20 260,20 420,70 C560,115 640,170 730,165 C770,162 800,140 814,122" fill="none" stroke="var(--brand)" stroke-width="4"/>
      <!-- decorative emblem area -->
      <g role="img" aria-label="Faint large decorative brand emblem in light grey">
        <rect x="255" y="565" width="535" height="460" rx="200" fill="url(#emblem-glow)"/>
      </g>
      <!-- footer band -->
      <path class="footer-band" d="M0,892 C150,870 320,960 450,1005 C560,1040 700,1030 814,962 V1052 H0 Z" fill="var(--band-soft)"/>
    </svg>

    <div class="brand-name">Meridian Realty Group, LLC</div>

    <div class="address">
      <svg class="address__icon" viewBox="0 0 14 13"><path d="M7 0 L14 6 H12 V13 H8.5 V9 H5.5 V13 H2 V6 H0 Z"/></svg>00, xxxxxx, xxxxxxx<br>xxxxxxx-0000
    </div>

    <ul class="contact-list">
      <li class="contact-list__item">
        <svg class="contact-list__icon contact-list__icon--solid" viewBox="0 0 12 12"><path d="M2.5 1 L4.5 1 L5.2 3.6 L4 4.6 C4.6 6 5.9 7.4 7.4 8 L8.4 6.8 L11 7.5 V9.5 C11 10.3 10.3 11 9.5 11 C5 11 1 7 1 2.5 C1 1.7 1.7 1 2.5 1 Z"/></svg>
        00 000 0000
      </li>
      <li class="contact-list__item">
        <svg class="contact-list__icon" viewBox="0 0 12 12"><rect x="3.2" y="0.8" width="5.6" height="10.4" rx="1"/><line x1="5.3" y1="9.4" x2="6.7" y2="9.4"/></svg>
        0000000000
      </li>
      <li class="contact-list__item">
        <svg class="contact-list__icon contact-list__icon--solid" viewBox="0 0 12 12"><path d="M0.5 2.5 H11.5 V9.5 H0.5 Z M1.3 3.2 L6 6.6 L10.7 3.2 V3 H1.3 Z" fill-rule="evenodd"/></svg>
        xxxxx@xxxx.xxx
      </li>
      <li class="contact-list__item">
        <svg class="contact-list__icon" viewBox="0 0 12 12"><circle cx="6" cy="6" r="5"/><ellipse cx="6" cy="6" rx="2.2" ry="5"/><line x1="1" y1="6" x2="11" y2="6"/></svg>
        xxx.xxxxxxxxxxxxx.xxx
      </li>
    </ul>
  </main>
</body>
</html>
```